Accounting firm needing business card / letterhead designed
Marcus L. Trenholm, CPA
marcus@veltrowledger.com
www.veltrowledger.com
842 E Alder Ave Calder Falls, IN 43827
419-562-0974

```html
<!DOCTYPE html>
<html lang="en">
<head>
<meta charset="UTF-8">
<title>Veltro Ledger – Business Card</title>
<link href="https://fonts.googleapis.com/css2?family=Orbitron:wght@500;700&family=Roboto:wght@400&display=swap" rel="stylesheet">
<style>
  :root {
    --backdrop: #121212;
    --card-light: #f7f7f7;
    --card-light-end: #e9e9e9;
    --navy: #27215e;
    --violet-top: #3f3795;
    --violet-bottom: #262060;
    --text-grey: #4a4a4a;
  }
  html, body {
    margin: 0;
    padding: 0;
    width: 1200px;
    height: 960px;
    overflow: hidden;
    background: var(--backdrop);
  }
  .stage {
    position: relative;
    width: 1200px;
    height: 960px;
  }
  .card {
    position: absolute;
    width: 600px;
    height: 343px;
    box-sizing: border-box;
  }
  .card-front {
    left: 302px;
    top: 129px;
    background: linear-gradient(90deg, var(--card-light), var(--card-light-end));
  }
  .card-back {
    left: 299px;
    top: 488px;
    background: linear-gradient(160deg, var(--violet-top), var(--violet-bottom));
  }
  .brand-name {
    position: absolute;
    left: 52px;
    top: 100px;
    margin: 0;
    font-family: "Orbitron", sans-serif;
    font-weight: 700;
    font-size: 26px;
    letter-spacing: 0.5px;
    line-height: 1;
    color: var(--navy);
  }
  .person-name {
    position: absolute;
    left: 51px;
    top: 166px;
    margin: 0;
    font-family: "Orbitron", sans-serif;
    font-weight: 500;
    font-size: 21px;
    line-height: 26px;
    color: var(--navy);
  }
  .contact-list {
    position: absolute;
    left: 52px;
    top: 205px;
    margin: 0;
    padding: 0;
    list-style: none;
    font-family: "Roboto", sans-serif;
    font-size: 14.5px;
    color: var(--text-grey);
  }
  .contact-list li {
    display: flex;
    align-items: center;
    height: 19.5px;
  }
  .contact-list svg {
    width: 14px;
    height: 14px;
    margin-right: 8px;
    fill: var(--navy);
  }
  .address {
    position: absolute;
    left: 50px;
    top: 275px;
    margin: 0;
    font-family: "Roboto", sans-serif;
    font-size: 14.5px;
    color: var(--text-grey);
  }
</style>
</head>
<body>
<main class="stage">
  <section class="card card-front">
    <p class="brand-name">VELTRO LEDGER</p>
    <h1 class="person-name">Marcus L. Trenholm, CPA</h1>
    <ul class="contact-list">
      <li>
        <svg viewBox="0 0 16 16" aria-hidden="true"><path d="M3.6 1.2l2.3 2.9-1.4 1.8c.9 2 2.5 3.6 4.6 4.6l1.8-1.4 2.9 2.3-1.3 2.4C7.6 13.6 2.4 8.4 1.2 2.5z"/></svg>
        555-562-0974
      </li>
      <li>
        <svg viewBox="0 0 16 16" aria-hidden="true"><path d="M1 3h14v1.2L8 8.6 1 4.2zM1 5.6l7 4.4 7-4.4V13H1z"/></svg>
        marcus@veltrowledger.com
      </li>
      <li>
        <svg viewBox="0 0 16 16" aria-hidden="true"><circle cx="8" cy="8" r="7"/><path d="M5 4.5l2 1-.5 2 1.5 1.5-1 2.5M10 3.5l.5 2 2 1" stroke="#f2f2f2" stroke-width="1.2" fill="none"/></svg>
        www.veltrowledger.com
      </li>
    </ul>
    <p class="address">842 E Alder Ave, Calder Falls, IN 43827</p>
  </section>
  <section class="card card-back" role="img" aria-label="Reverse side with a repeating diagonal brand-name pattern in violet tones"></section>
</main>
</body>
</html>
```